Fresh, modern, fun business card for pediatric dental practice

Need a business card for fresh, modern, fun pediatric dental practice

Clean look that matches our website's font and colors

We prefer the look of curved corners on business cards

Target Market(s)

parents (mothers) of young children, professionals, mid-high class

Industry/Entity Type

Dental

Contact Information for Business Card

Maplebrook Pediatric Dentistry
482 Quarry Lane
Suite 517
Fernwood, PA 17590
717.555.0193
www.maplebrookkidsdental.example

Mei-Ran Tsai, DMD
Corinne Walbeck, DMD
(we are working on our email address, but we would like that on the card as well)

Font styles to use
Sans Serif

Requirements
Must have
• All info; we would also like to make cards for individual staff members
• colors from our website and color palatte, attatched
• use same font and design as website for branding
Nice to have
• clean, simple card that has a pop of color
• we would like to see a few designs with our tag line "where smiles get brighter"
• we are not sure if we want to have it on there or not
• we would like to see a few designs incorporating the ribbon graphic on our website where the word WELCOME is

```html
<!DOCTYPE html>
<html lang="en">
<head>
<meta charset="utf-8">
<title>Maplebrook Pediatric Dentistry – Business Card</title>
<link rel="stylesheet" href="https://fonts.googleapis.com/css2?family=Roboto+Condensed:wght@700&family=Roboto:wght@400&family=Open+Sans:wght@400;600&display=swap">
<style>
  :root {
    --backdrop: #2a2a2a;
    --magenta: #c92f8b;
    --sun: #f0b125;
    --paper: #f3f3f3;
    --white: #ffffff;
  }
  * { margin: 0; padding: 0; box-sizing: border-box; }
  html, body { width: 1200px; height: 960px; overflow: hidden; }
  body { background: var(--backdrop); position: relative; }

  .card {
    position: absolute;
    width: 600px;
    height: 342px;
    border-radius: 18px;
    overflow: hidden;
  }
  .card-front { left: 314px; top: 113px; background: var(--magenta); }
  .card-back  { left: 311px; top: 472px; background: var(--paper); }

  .sun-decoration { position: absolute; left: 0; top: 0; }

  .dentists {
    position: absolute;
    left: 35px;
    top: 133px;
    font-family: "Roboto Condensed", "Arial Narrow", sans-serif;
    font-weight: 700;
    font-size: 20px;
    line-height: 24px;
    color: var(--sun);
  }
  .practice-address {
    position: absolute;
    left: 35px;
    top: 192px;
    font-family: "Roboto", Arial, sans-serif;
    font-size: 14.5px;
    line-height: 18px;
    color: var(--white);
    font-style: normal;
  }
  .contact-list {
    position: absolute;
    left: 35px;
    top: 276px;
    list-style: none;
    font-family: "Roboto", Arial, sans-serif;
    font-size: 14.5px;
    line-height: 20px;
    color: var(--white);
  }
  .contact-list li { display: flex; align-items: center; gap: 7px; }
  .contact-icon { width: 13px; height: 13px; flex: none; }

  .brand {
    position: absolute;
    left: 0; right: 0;
    top: 70px;
    text-align: center;
    font-family: "Open Sans", Arial, sans-serif;
  }
  .brand-dot {
    display: block;
    width: 46px; height: 46px;
    margin: 0 auto 50px;
    border-radius: 50%;
    background: var(--sun);
  }
  .brand-name {
    display: block;
    font-weight: 600;
    font-size: 54px;
    line-height: 58px;
    letter-spacing: 0.5px;
    color: var(--sun);
  }
  .brand-line {
    display: block;
    margin-top: 2px;
    font-weight: 400;
    font-size: 28px;
    line-height: 34px;
    letter-spacing: 1px;
    color: var(--magenta);
  }
</style>
</head>
<body>
  <section class="card card-front">
    <svg class="sun-decoration" width="600" height="342" viewBox="0 0 600 342" aria-hidden="true">
      <circle cx="466" cy="109" r="135" fill="var(--sun)"/>
    </svg>

    <p class="dentists">Mei-Ran Tsai, DMD<br>Corinne Walbeck, DMD</p>

    <address class="practice-address">
      Maplebrook Pediatric Dentistry<br>
      482 Quarry Lane<br>
      Suite 517<br>
      Fernwood, PA 17590
    </address>

    <ul class="contact-list">
      <li>
        <svg class="contact-icon" viewBox="0 0 24 24" aria-hidden="true">
          <path fill="var(--sun)" d="M6.6 10.8a15.1 15.1 0 0 0 6.6 6.6l2.2-2.2a1 1 0 0 1 1-.25 11.4 11.4 0 0 0 3.6.57 1 1 0 0 1 1 1V20a1 1 0 0 1-1 1A17 17 0 0 1 3 4a1 1 0 0 1 1-1h3.5a1 1 0 0 1 1 1c0 1.250.2 2.450.57 3.57a1 1 0 0 1-.25 1z"/>
        </svg>
        717.555.0193
      </li>
      <li>
        <svg class="contact-icon" viewBox="0 0 24 24" aria-hidden="true">
          <circle cx="12" cy="12" r="10" fill="var(--sun)"/>
          <path fill="none" stroke="var(--magenta)" stroke-width="1.6" d="M2 12h20M12 2c3 3 3 17 0 20M12 2c-3 3-3 17 0 20"/>
        </svg>
        maplebrookkidsdental.example
      </li>
    </ul>
  </section>

  <section class="card card-back">
    <div class="brand">
      <span class="brand-dot"></span>
      <span class="brand-name">maplebrook</span>
      <span class="brand-line">pediatric dentistry</span>
    </div>
  </section>
</body>
</html>
```